Pine Hollow Haven Home Inc. Website Update

We have a couple of broken links such as the "contact us" and would like to add board members and a calendar of events. We are open to a new design.

```html
<!DOCTYPE html>
<html lang="en">
<head>
<meta charset="utf-8">
<title>Pine Hollow Haven Home Inc.</title>
<link rel="stylesheet" href="https://fonts.googleapis.com/css2?family=Marcellus+SC&family=Poppins:wght@400;500;600;700&display=swap">
<style>
:root{
  --blue:#1f5ea8;
  --blue-dark:#174a88;
  --blue-light:#2f7bc8;
  --pink:#e0157d;
  --pink-dark:#c70f6c;
  --ink:#333;
  --grey:#666;
  --line:#d8d8d8;
  --white:#fff;
  --black:#111;
}
*{box-sizing:border-box;margin:0;padding:0}
html,body{width:1200px;height:5085px;overflow:hidden}
body{font-family:"Poppins",sans-serif;color:var(--ink);background:var(--white);position:relative}
.heading{font-family:"Marcellus SC",serif;font-weight:400;letter-spacing:2px}
section,header,footer,nav,.topbar{position:absolute;left:0;width:1200px}
.btn{display:inline-block;border-radius:30px;color:var(--white);font-weight:600;font-size:15px;letter-spacing:1px;text-transform:uppercase;text-align:center}

/* top bar */
.topbar{top:0;height:34px;background:var(--blue)}
.topbar .social{position:absolute;left:110px;top:10px;display:flex;gap:12px}
.topbar .social span{width:13px;height:13px;border-radius:50%;background:var(--white);opacity:.9}
.topbar .address{position:absolute;right:100px;top:7px;color:var(--white);font-size:13px}
/* header */
.site-header{top:34px;height:116px}
.contact-chip{position:absolute;top:36px;display:flex;gap:12px;align-items:center}
.contact-chip.call{left:210px}
.contact-chip.mail{left:778px}
.contact-chip .label{color:var(--pink);font-weight:600;font-size:15px}
.contact-chip .value{font-size:13px;color:var(--ink)}
.brand{position:absolute;left:500px;top:6px;width:200px;height:150px;text-align:center;z-index:3}
.brand .mark{width:130px;height:130px;border-radius:50%;background:var(--pink);margin:0 auto;display:flex;align-items:center;justify-content:center;color:var(--white);font-weight:600;font-size:14px;line-height:1.35;padding:14px;border:6px solid var(--white);box-shadow:0 0 0 2px var(--pink)}
/* nav */
.main-nav{top:150px;height:60px;border-top:1px solid var(--line)}
.main-nav ul{list-style:none;position:absolute;top:20px;width:100%;font-family:"Marcellus SC",serif;font-size:17px;color:var(--ink)}
.main-nav li{position:absolute;white-space:nowrap}
/* hero */
.hero{top:210px;height:690px;overflow:hidden}
.hero .photo{position:absolute;inset:0;background:linear-gradient(160deg,#8a5a48 0%,#b5866c 35%,#c9b8a5 60%,#7e6c62 100%)}
.hero h1{position:absolute;top:150px;width:100%;text-align:center;color:var(--white);font-size:62px;text-shadow:0 2px 8px rgba(0,0,0,.35)}
.hero .btn{position:absolute;left:487px;top:238px;width:226px;height:46px;line-height:46px;background:var(--pink)}
.hero svg{position:absolute;left:0;bottom:0}
/* about */
.about{top:1000px;height:480px}
.about .badge{position:absolute;left:78px;top:20px;width:455px;height:455px;border-radius:50%;border:8px solid var(--pink);display:flex;align-items:center;justify-content:center}
.about .badge .inner{width:420px;height:420px;border-radius:50%;background:radial-gradient(circle,#d24a8b 0%,#b8326f 55%,#8f2f5a 100%);display:flex;align-items:center;justify-content:center;color:var(--white);font-weight:600;font-size:26px;text-align:center;line-height:1.4}
.about h2{position:absolute;left:578px;top:40px;color:var(--pink);font-size:40px}
.about p{position:absolute;left:578px;top:100px;width:540px;font-size:14px;line-height:2.05;color:var(--grey)}
.about .btn{position:absolute;left:578px;top:398px;width:186px;height:54px;line-height:54px;background:var(--blue-dark)}
/* services */
.services{top:1560px;height:700px}
.services svg{position:absolute;left:0;top:0}
.services h2{position:absolute;top:118px;width:100%;text-align:center;color:var(--white);font-size:40px}
.services .lead{position:absolute;top:180px;width:100%;text-align:center;color:var(--white);font-size:15px;line-height:1.9}
.service{position:absolute;top:268px;width:250px;text-align:center}
.service .ring{width:226px;height:226px;margin:0 auto;border-radius:50%;border:4px solid var(--pink);display:flex;align-items:center;justify-content:center}
.service .disc{width:196px;height:196px;border-radius:50%;background:var(--pink);display:flex;align-items:center;justify-content:center}
.service .icon{width:120px;height:120px;border-radius:50%;background:var(--white)}
.service h3{margin-top:14px;color:var(--white);font-family:"Marcellus SC",serif;font-weight:400;font-size:20px;line-height:1.3;letter-spacing:1px}
/* events */
.events{top:2340px;height:460px}
.events h2{position:absolute;left:98px;top:76px;color:var(--pink);font-size:40px}
.events p{position:absolute;left:98px;top:130px;width:505px;font-size:14px;line-height:2;color:var(--grey)}
.events .btn{position:absolute;left:98px;top:312px;width:190px;height:56px;line-height:56px;background:var(--blue-dark)}
.events .halo{position:absolute;left:665px;top:38px;width:420px;height:420px;border-radius:50%;background:var(--pink);box-shadow:inset 0 0 0 10px var(--pink-dark)}
.calendar{position:absolute;left:675px;top:22px;width:415px;height:400px;background:var(--white);box-shadow:0 4px 14px rgba(0,0,0,.25)}
.calendar .cal-head{height:50px;background:var(--blue);color:var(--white);font-size:28px;text-align:center;line-height:50px;position:relative}
.calendar .cal-head .arrow{position:absolute;top:9px;width:32px;height:32px}
.calendar .days,.calendar .dates{display:grid;grid-template-columns:repeat(7,1fr);text-align:center}
.calendar .days{height:38px;line-height:38px;color:#888;font-size:17px}
.calendar .dates div{height:56px;line-height:56px;font-size:27px;color:var(--black);border-right:1px solid #e6e6e6;border-bottom:1px solid #e6e6e6}
.calendar .dates .today{background:#333;color:var(--white)}
/* board */
.board{top:2880px;height:700px}
.board svg{position:absolute;left:0;top:0}
.board h2{position:absolute;top:118px;width:100%;text-align:center;color:var(--white);font-size:34px}
.board .lead{position:absolute;top:168px;left:160px;width:880px;text-align:center;color:var(--white);font-size:15px;line-height:2}
.member{position:absolute;top:258px;width:240px;text-align:center;color:var(--white)}
.member .portrait{width:232px;height:232px;margin:0 auto;border-radius:50%;border:4px solid var(--white);background:radial-gradient(circle at 50% 40%,#c9a58f 0%,#8d6b58 55%,#4e3b33 100%)}
.member h3{font-family:"Marcellus SC",serif;font-weight:400;font-size:22px;letter-spacing:1px;margin-top:8px;line-height:1.2}
.member span{font-size:13px;letter-spacing:1px;text-transform:uppercase}
/* contact */
.contact{top:3640px;height:400px}
.contact h2{position:absolute;top:0;width:100%;text-align:center;color:var(--pink);font-size:40px}
.contact-form{position:absolute;left:165px;top:90px;width:870px}
.field{position:absolute;height:44px;border-bottom:1px solid var(--line);font-size:13px;color:#555;padding:10px 0 0 14px;background:var(--white)}
.field.msg{height:152px;border:1px solid var(--line)}
.contact .btn{position:absolute;left:520px;top:313px;width:160px;height:48px;line-height:48px;background:var(--blue-dark)}
/* testimonials */
.testimonials{top:4070px;height:620px}
.testimonials svg.band{position:absolute;left:0;top:0}
.testimonials h2{position:absolute;top:160px;width:100%;text-align:center;color:var(--white);font-size:40px;line-height:1.1}
.testimonials .quote-mark{position:absolute;left:570px;top:228px}
.testimonials .quote{position:absolute;left:170px;top:282px;width:860px;text-align:center;color:var(--white);font-size:18px;line-height:1.8}
.testimonials .author{position:absolute;top:410px;width:100%;text-align:center;color:var(--white);font-weight:600;font-size:16px}
.testimonials .nav-arrow{position:absolute;top:296px}
/* footer */
.site-footer{top:4680px;height:355px;background:var(--pink)}
.site-footer .brand-foot{position:absolute;left:88px;top:68px;width:170px;text-align:center}
.site-footer .brand-foot .mark{width:150px;height:150px;margin:0 auto;border-radius:50%;border:5px solid var(--white);display:flex;align-items:center;justify-content:center;color:var(--white);font-weight:600;font-size:15px;line-height:1.35;padding:12px}
.site-footer .social{display:flex;gap:12px;justify-content:center;margin-top:16px}
.site-footer .social span{width:28px;height:28px;border-radius:50%;border:2px solid var(--white)}
.foot-col{position:absolute;top:72px;color:var(--white)}
.foot-col h4{font-family:"Marcellus SC",serif;font-weight:400;font-size:20px;letter-spacing:2px;margin-bottom:22px}
.foot-col li{list-style:none;font-size:13px;margin-bottom:14px;display:flex;gap:10px;align-items:flex-start}
.foot-col p{font-size:12px;line-height:1.6;width:310px}
.foot-col .email-input{margin-top:16px;width:310px;height:42px;background:var(--white);font-size:12px;color:#888;padding:12px 14px}
.foot-col .btn{margin-top:14px;width:110px;height:40px;line-height:40px;background:var(--blue-dark);border-radius:4px;font-size:14px}
.quick li{font-size:13px;margin-bottom:10px}
.bottom-bar{position:absolute;left:0;top:5035px;width:1200px;height:50px;background:var(--black);color:#ddd;font-size:13px;text-align:center;line-height:50px}
</style>
</head>
<body>

<div class="topbar">
  <div class="social"><span></span><span></span><span></span><span></span><span></span><span></span></div>
  <div class="address">&#9679; 418 Cedar Ridge Rd, Millbrook, GA 30999, USA</div>
</div>

<header class="site-header">
  <div class="contact-chip call">
    <svg width="36" height="36" viewBox="0 0 24 24"><circle cx="12" cy="12" r="11" fill="none" stroke="#e0157d" stroke-width="1.6"/><path d="M8 6.5l2 .2 1 2.6-1.3 1.1a7 7 0 0 0 3.9 3.9l1.1-1.3 2.6 1 .2 2c-4.8.8-10.2-4.6-9.5-9.5z" fill="#e0157d"/></svg>
    <div><div class="label">Call us:</div><div class="value">555.014.2270</div></div>
  </div>
  <div class="brand"><div class="mark">Pine Hollow Haven Home Inc.</div></div>
  <div class="contact-chip mail">
    <svg width="40" height="30" viewBox="0 0 40 30"><rect x="2" y="3" width="36" height="24" rx="3" fill="none" stroke="#e0157d" stroke-width="2.4"/><path d="M3 5l17 13L37 5" fill="none" stroke="#e0157d" stroke-width="2.4"/></svg>
    <div><div class="label">Mail us:</div><div class="value">hello@pinehollowhaven.org</div></div>
  </div>
</header>

<nav class="main-nav">
  <ul>
    <li style="left:96px">About</li>
    <li style="left:190px">How You Can Help</li>
    <li style="left:398px">Services</li>
    <li style="left:705px">Our Love of Pets</li>
    <li style="left:893px">Contact</li>
    <li style="left:1008px">Haven Walk</li>
  </ul>
</nav>

<section class="hero">
  <div class="photo" role="img" aria-label="Photo of teenage girls reading and studying together on brick steps outside a building"></div>
  <h1 class="heading">HAVEN HOME INC</h1>
  <a class="btn">&#9829; Donate Now</a>
  <svg width="1200" height="140" viewBox="0 0 1200 140">
    <path d="M0 40 Q600 150 1200 40 L1200 140 L0 140Z" fill="#fff"/>
    <path d="M90 90 Q600 10 1110 90" fill="none" stroke="#1f5ea8" stroke-width="7"/>
    <path d="M120 104 Q600 34 1080 104" fill="none" stroke="#1f5ea8" stroke-width="4"/>
    <path d="M150 116 Q600 56 1050 116" fill="none" stroke="#1f5ea8" stroke-width="2"/>
  </svg>
</section>

<section class="about">
  <div class="badge"><div class="inner" role="img" aria-label="Photo of residents standing in a circle, overlaid with the home's anniversary badge">Pine Hollow<br>Haven Home Inc.</div></div>
  <h2 class="heading">ABOUT US</h2>
  <p>Pine Hollow Haven Home is home to 31 girls ranging in ages from 12-21. The home has seven bedrooms and four bathrooms with a large spa tub for relaxing. Our kitchen takes on the aroma of a restaurant in the evenings as the girls practice their Independent Living Skills with menu planning and preparation in a supervised setting. When the girls are not cooking or relaxing in their rooms, they may be found in the family room where community meetings are held to problem solve. Community Meetings consist of problem solving skills and real life issues that the girls share with others to seek input from their peers.</p>
  <a class="btn">Read More</a>
</section>

<section class="services">
  <svg width="1200" height="700" viewBox="0 0 1200 700">
    <path d="M0 60 Q300 -10 620 40 T1200 20 L1200 600 Q600 720 0 640Z" fill="#1f5ea8"/>
    <path d="M0 90 Q400 20 800 70 T1200 60 L1200 110 Q700 40 0 140Z" fill="#2f7bc8" opacity=".45"/>
    <path d="M0 600 Q600 700 1200 560 L1200 610 Q600 730 0 650Z" fill="#2f7bc8" opacity=".5"/>
  </svg>
  <h2 class="heading">WE ARE PINE HOLLOW HAVEN HOME</h2>
  <div class="lead">With the help of our community, we have raised over 1000 girls and counting!<br>Some of the services we offer include:</div>
  <div class="service" style="left:84px"><div class="ring"><div class="disc"><div class="icon" role="img" aria-label="Icon of a lit bulb"></div></div></div><h3>Room, Board, and<br>Watchful Oversight</h3></div>
  <div class="service" style="left:349px"><div class="ring"><div class="disc"><div class="icon" role="img" aria-label="Icon of a heart"></div></div></div><h3>Transitional<br>Living Services</h3></div>
  <div class="service" style="left:614px"><div class="ring"><div class="disc"><div class="icon" role="img" aria-label="Icon of a young woman"></div></div></div><h3>Independent<br>Living Services</h3></div>
  <div class="service" style="left:866px"><div class="ring"><div class="disc"><div class="icon" role="img" aria-label="Icon of a handshake"></div></div></div><h3>Foster<br>Gift Shop</h3></div>
</section>

<section class="events">
  <h2 class="heading">CALENDAR OF EVENTS</h2>
  <p>Sed ut perspiciatis unde omnis iste natus error sit voluptatem accusantium doloremque laudantium, totam rem aperiam, eaque ipsa quae ab illo inventore veritatis et quasi architecto beatae vitae dicta sunt explicabo. Nemo enim ipsam voluptatem quia voluptas sit aspernatur aut odit aut fugit, sed quia consequuntur magni dolores eos qui ratione voluptatem sequi nesciunt.</p>
  <a class="btn">Book Event</a>
  <div class="halo"></div>
  <div class="calendar">
    <div class="cal-head">
      <svg class="arrow" style="left:8px" viewBox="0 0 32 32"><path d="M20 6L10 16l10 10" fill="none" stroke="#fff" stroke-width="4"/></svg>
      Feb 2019
      <svg class="arrow" style="right:8px" viewBox="0 0 32 32"><path d="M12 6l10 10-10 10" fill="none" stroke="#fff" stroke-width="4"/></svg>
    </div>
    <div class="days"><div>SUN</div><div>MON</div><div>TUE</div><div>WED</div><div>THU</div><div>FRI</div><div>SAT</div></div>
    <div class="dates">
      <div></div><div></div><div></div><div></div><div></div><div>1</div><div>2</div>
      <div>3</div><div>4</div><div>5</div><div>6</div><div>7</div><div>8</div><div>9</div>
      <div>10</div><div>11</div><div>12</div><div>13</div><div>14</div><div>15</div><div>16</div>
      <div>17</div><div>18</div><div>19</div><div>20</div><div>21</div><div>22</div><div>23</div>
      <div>24</div><div>25</div><div>26</div><div class="today">27</div><div>28</div><div></div><div></div>
    </div>
  </div>
</section>

<section class="board">
  <svg width="1200" height="700" viewBox="0 0 1200 700">
    <path d="M0 40 Q600 -30 1200 60 L1200 680 Q600 560 0 640Z" fill="#e0157d"/>
    <path d="M0 70 Q600 0 1200 90 L1200 120 Q600 30 0 100Z" fill="#c70f6c" opacity=".5"/>
    <path d="M0 600 Q600 540 1200 640 L1200 680 Q600 560 0 640Z" fill="#c70f6c" opacity=".6"/>
  </svg>
  <h2 class="heading">BOARD MEMBERS</h2>
  <div class="lead">Sed ut perspiciatis unde omnis iste natus error sit voluptatem accusantium doloremque laudantium, totam rem aperiam, eaque ipsa quae ab illo inventore veritatis et quasi.</div>
  <div class="member" style="left:103px"><div class="portrait" role="img" aria-label="Portrait photo of the board chairman"></div><h3>HARLOW</h3><span>Chairman</span></div>
  <div class="member" style="left:360px"><div class="portrait" role="img" aria-label="Portrait photo of the CEO"></div><h3>CELESTE</h3><span>CEO</span></div>
  <div class="member" style="left:617px"><div class="portrait" role="img" aria-label="Portrait photo of the secretary"></div><h3>DEAN WALSH</h3><span>Secretary</span></div>
  <div class="member" style="left:874px"><div class="portrait" role="img" aria-label="Portrait photo of the secretary"></div><h3>NORA LANE</h3><span>Secretary</span></div>
</section>

<section class="contact">
  <h2 class="heading">CONTACT US</h2>
  <div class="contact-form">
    <div class="field" style="left:0;top:0;width:425px">&#9679; First Name</div>
    <div class="field" style="left:445px;top:0;width:425px">&#9679; Last Name</div>
    <div class="field" style="left:0;top:54px;width:425px">&#9679; Company Name</div>
    <div class="field" style="left:0;top:108px;width:425px">&#9679; Email Address</div>
    <div class="field" style="left:0;top:162px;width:425px">&#9679; Phone Number</div>
    <div class="field msg" style="left:445px;top:54px;width:425px">&#9679; Message</div>
  </div>
  <a class="btn">&#10148; Submit</a>
</section>

<section class="testimonials">
  <svg class="band" width="1200" height="620" viewBox="0 0 1200 620">
    <path d="M0 110 Q600 -40 1200 110 L1200 620 L0 620Z" fill="#1f5ea8"/>
    <path d="M0 140 Q600 0 1200 140 L1200 170 Q600 40 0 170Z" fill="#2f7bc8" opacity=".5"/>
  </svg>
  <h2 class="heading">TESTIMONIALS</h2>
  <svg class="quote-mark" width="60" height="44" viewBox="0 0 60 44"><path d="M4 40V24C4 12 10 5 22 3v7c-6 2-9 6-9 12h9v18zM34 40V24c0-12 6-19 18-21v7c-6 2-9 6-9 12h9v18z" fill="#fff"/></svg>
  <div class="quote">Sed ut perspiciatis unde omnis iste natus error sit voluptatem accusantium doloremque laudantium, totam rem aperiam, eaque ipsa quae ab illo inventore veritatis et quasi architecto beatae vitae dicta sunt explicabo.</div>
  <div class="author">Daniel Reyes</div>
  <svg class="nav-arrow" style="left:60px" width="70" height="40" viewBox="0 0 70 40"><path d="M68 20H6M22 4L5 20l17 16" fill="none" stroke="#fff" stroke-width="4"/></svg>
  <svg class="nav-arrow" style="left:1070px" width="70" height="40" viewBox="0 0 70 40"><path d="M2 20h62M48 4l17 16-17 16" fill="none" stroke="#fff" stroke-width="4"/></svg>
</section>

<footer class="site-footer">
  <div class="brand-foot">
    <div class="mark">Pine Hollow Haven Home Inc.</div>
    <div class="social"><span></span><span></span><span></span><span></span></div>
  </div>
  <div class="foot-col" style="left:315px">
    <h4>CONTACT US</h4>
    <ul>
      <li><span>&#9679;</span><span>418 Cedar Ridge Rd, Millbrook,<br>GA 30999, USA</span></li>
      <li><span>&#9742;</span><span>Phone: 555.014.2270</span></li>
      <li><span>&#9993;</span><span>Email: hello@pinehollowhaven.org</span></li>
    </ul>
  </div>
  <div class="foot-col" style="left:605px">
    <h4>SIGN UP FOR NEWSLETTER</h4>
    <p>Get monthly news from our home, upcoming events and simple ways to help our girls.</p>
    <div class="email-input">Enter email</div>
    <a class="btn">Sign Up</a>
  </div>
  <div class="foot-col quick" style="left:960px">
    <h4>QUICK LINKS</h4>
    <ul>
      <li>&#8226; About</li>
      <li>&#8226; How You Can Help</li>
      <li>&#8226; Services Offered</li>
      <li>&#8226; Our Love of Pets</li>
      <li>&#8226; Contact Us</li>
      <li>&#8226; Haven Walk</li>
    </ul>
  </div>
</footer>
<div class="bottom-bar">Copyright &copy; 2019 All Rights Reserved</div>

</body>
</html>
```